Website Quibrel Outdoor

Hi I'm looking for a simple design for a new website. It's outdoor products mainly in category, Boat, Tarpaulin, Fishing, Golf. I have include image and text for 8 products + presentation etc. I want a simple and modern site + fast + Mobile. Wordpress. I'm going to sell through Tradovik so I don't need any WooCommerce but a buy button to Tradovik. I haven set up the Tradovik account yet. My logo i s grey and orange. My goal is to sell in Tradovik US and later EU.

```html
<!DOCTYPE html>
<html lang="en">
<head>
<meta charset="utf-8">
<title>Quibrel Outdoor</title>
<link href="https://fonts.googleapis.com/css2?family=Montserrat:ital,wght@0,400;0,500;0,600;0,700;1,400&display=swap" rel="stylesheet">
<style>
:root{
  --orange:#f2861f;
  --dark:#1f1f1f;
  --topbar:#555555;
  --text:#222222;
  --muted:#666666;
  --light:#f2f2f2;
  --white:#ffffff;
  --line:#e6e6e6;
}
*{box-sizing:border-box;margin:0;padding:0}
html,body{width:1200px;height:3866px;overflow:hidden}
body{font-family:'Montserrat',sans-serif;color:var(--text);background:var(--white);position:relative}
.wrap{width:978px;margin:0 auto;position:relative}
a{color:inherit;text-decoration:none}

.topbar{height:38px;background:var(--topbar);color:#eee;font-size:14px}
.topbar .wrap{display:flex;align-items:center;height:38px;gap:22px}
.topbar .social{margin-left:auto;display:flex;gap:12px}
.topbar .social span{width:12px;height:12px;border-radius:50%;background:#eee;display:block}
.ico{display:inline-flex;align-items:center;gap:6px}

.header{height:73px;border-bottom:1px solid var(--line)}
.header .wrap{display:flex;align-items:center;height:73px}
.brand{display:flex;align-items:center;gap:10px;font-weight:700;font-size:26px;color:var(--orange);letter-spacing:.5px}
.brand .mark{width:54px;height:54px;border-radius:50%;background:#5d5d5d}
.nav{margin-left:auto;display:flex;gap:24px;font-size:15.5px;font-weight:600;text-transform:uppercase}
.tools{display:flex;gap:10px;margin-left:36px}
.tools span{width:33px;height:33px;border:1px solid #ccc;border-radius:50%;display:flex;align-items:center;justify-content:center}

.hero{height:662px;position:relative;background:linear-gradient(180deg,#8aa0b8 0%,#58728e 35%,#2e4a6c 60%,#1c2f48 100%)}
.hero .wrap{padding-top:262px;color:var(--white)}
.hero h1{font-size:48px;font-weight:700;letter-spacing:.5px}
.hero p{font-size:19px;font-weight:500;line-height:1.45;width:440px;margin-top:10px}
.btn-orange{display:inline-block;margin-top:28px;background:var(--orange);color:var(--white);font-weight:700;font-size:16px;padding:13px 27px}
.arrow{position:absolute;top:50%;transform:translateY(-50%)}

.section-title{text-align:center;font-size:35px;font-weight:700;text-transform:uppercase;letter-spacing:.3px}
.categories{height:559px;padding-top:78px}
.cat-row{display:flex;gap:20px;margin-top:28px}
.cat{width:313px;text-align:center}
.cat .photo{height:244px}
.cat h3{font-size:26px;font-weight:500;margin-top:12px}
.cat p{font-size:14.5px;color:var(--muted);line-height:1.7;margin-top:4px}

.featured{height:534px;background:var(--light);padding-top:66px}
.prod-row{display:flex;gap:23px;margin-top:40px}
.prod{width:227px;text-align:center;font-size:15px}
.prod .photo{height:260px;background:var(--white);border:1px solid #e3e3e3;display:flex;align-items:center;justify-content:center}
.prod .name{margin-top:13px;font-weight:500}
.prod .price{margin-top:8px;font-weight:500}

.about{height:479px;display:flex}
.about .photo{width:600px;height:479px}
.about .copy{width:600px;background:var(--orange);color:var(--white);padding:68px 0 0 72px}
.about h2{font-size:35px;font-weight:700}
.about p{font-size:14.5px;line-height:1.75;width:420px;margin-top:14px}
.btn-outline{display:inline-block;border:2px solid var(--white);padding:13px 26px;font-weight:700;font-size:16px;margin-top:28px;margin-left:6px}

.reviews{height:433px;padding-top:82px}
.rev-row{display:flex;gap:17px;margin-top:38px}
.rev{width:315px;height:200px;background:var(--white);box-shadow:0 0 8px rgba(0,0,0,.12);padding:20px 22px}
.rev .who{display:flex;align-items:center;gap:16px}
.rev .avatar{width:62px;height:62px;border-radius:50%;background:#b9b2aa}
.rev .who b{font-size:16px;font-weight:600}
.rev .stars{display:flex;gap:2px;margin-top:4px}
.rev p{font-style:italic;font-size:14px;color:#444;line-height:1.8;margin-top:12px}

.newsletter{height:129px;background:var(--orange)}
.newsletter .wrap{display:flex;align-items:center;height:129px}
.newsletter h2{color:var(--white);font-size:27px;font-weight:700}
.news-form{margin-left:auto;display:flex;width:489px;height:44px;background:var(--white);border:2px solid var(--white)}
.news-form .field{flex:1;font-size:12px;padding:0 16px;display:flex;align-items:center;color:#333}
.news-form .submit{background:var(--orange);color:var(--white);font-weight:700;font-size:15px;padding:0 10px;display:flex;align-items:center}

.blog{height:582px;padding-top:76px}
.blog-row{display:flex;gap:12px;margin-top:28px}
.post{width:318px}
.post .photo{height:244px}
.post h3{font-size:16px;font-weight:600;line-height:1.4;margin-top:16px}
.post p{font-size:14px;color:#444;line-height:1.55;margin-top:9px}
.post p a{color:var(--orange);font-weight:600}

.footer{height:377px;background:var(--dark);color:var(--white)}
.footer .wrap{display:flex;padding-top:80px;height:307px}
.foot-brand{width:403px}
.foot-brand .brand{color:var(--white);font-size:34px;gap:14px}
.foot-brand .brand .mark{background:var(--white);width:70px;height:70px}
.contact{margin-top:36px;font-size:16px;line-height:29px}
.contact div{display:flex;align-items:center;gap:8px}
.col{font-size:14.5px}
.col h4{font-size:17px;font-weight:700;text-transform:uppercase;margin-bottom:8px}
.col li{list-style:none;line-height:29px}
.c1{width:227px}.c2{width:250px}
.bottom{border-top:1px solid #3a3a3a}
.bottom .wrap{display:flex;align-items:center;height:70px;font-size:14px}
.cards{margin-left:auto;display:flex;gap:7px}
.cards span{width:30px;height:20px;background:#d8d8d8;border-radius:2px;display:block}
</style>
</head>
<body>

<div class="topbar">
  <div class="wrap">
    <span class="ico"><svg width="12" height="12" viewBox="0 0 24 24"><path fill="#eee" d="M6.6 10.8a15 15 0 0 0 6.6 6.6l2.2-2.2a1 1 0 0 1 1-.25 11.4 11.4 0 0 0 3.6.57 1 1 0 0 1 1 1V20a1 1 0 0 1-1 1A17 17 0 0 1 3 4a1 1 0 0 1 1-1h3.5a1 1 0 0 1 1 1c0 1.25.2 2.45.57 3.57a1 1 0 0 1-.25 1z"/></svg>(+155) 204 3817</span>
    <span class="ico"><svg width="14" height="11" viewBox="0 0 14 11"><rect width="14" height="11" rx="1" fill="#eee"/><path d="M0 1l7 5 7-5" stroke="#555" stroke-width="1.3" fill="none"/></svg>info@quibreloutdoor.com</span>
    <div class="social"><span></span><span></span><span></span></div>
  </div>
</div>

<header class="header">
  <div class="wrap">
    <div class="brand"><span class="mark"></span>QUIBREL OUTDOOR</div>
    <nav class="nav"><a>Home</a><a>Shop</a><a>About Us</a><a>Review</a><a>Blog</a><a>Contact Us</a></nav>
    <div class="tools">
      <span><svg width="15" height="15" viewBox="0 0 16 16"><circle cx="7" cy="7" r="5" stroke="#333" stroke-width="1.6" fill="none"/><path d="M11 11l4 4" stroke="#333" stroke-width="1.6"/></svg></span>
      <span><svg width="15" height="15" viewBox="0 0 16 16"><path d="M1 2h2.5l2 8h8l1.5-6H4.5" stroke="#333" stroke-width="1.4" fill="none"/><circle cx="6.5" cy="13.5" r="1.2" fill="#333"/><circle cx="12.5" cy="13.5" r="1.2" fill="#333"/></svg></span>
      <span><svg width="15" height="15" viewBox="0 0 16 16"><circle cx="8" cy="5" r="3" stroke="#333" stroke-width="1.4" fill="none"/><path d="M2 15c0-3.5 2.7-5.5 6-5.5s6 2 6 5.5" stroke="#333" stroke-width="1.4" fill="none"/></svg></span>
    </div>
  </div>
</header>

<section class="hero" role="img" aria-label="Angler casting a fishing rod from a boat on a lake">
  <svg class="arrow" style="left:64px" width="24" height="44" viewBox="0 0 24 44"><path d="M22 2L2 22l20 20" stroke="#fff" stroke-width="2" fill="none"/></svg>
  <svg class="arrow" style="right:70px" width="24" height="44" viewBox="0 0 24 44"><path d="M2 2l20 20L2 42" stroke="#fff" stroke-width="2" fill="none"/></svg>
  <div class="wrap">
    <h1>QUIBREL OUTDOOR</h1>
    <p>Lorem ipsum dolor sit amet, csectetur aiscing elit, sed do eiusmod</p>
    <a class="btn-orange">BUY ON TRADOVIK</a>
  </div>
</section>

<section class="categories">
  <div class="wrap">
    <h2 class="section-title">Shop by Category</h2>
    <svg class="arrow" style="left:-38px;top:372px" width="16" height="30" viewBox="0 0 16 30"><path d="M15 1L1 15l14 14" stroke="#333" stroke-width="2" fill="none"/></svg>
    <svg class="arrow" style="right:-38px;top:372px" width="16" height="30" viewBox="0 0 16 30"><path d="M1 1l14 14L1 29" stroke="#333" stroke-width="2" fill="none"/></svg>
    <div class="cat-row">
      <div class="cat"><div class="photo" role="img" aria-label="Boat console with steering wheel" style="background:linear-gradient(160deg,#e6e6e6,#8e9195 60%,#4a4c50)"></div><h3>BOAT</h3><p>Lorem ipsum dolor sit amet, consectetur adipiscing elit, sed do eiusmod</p></div>
      <div class="cat"><div class="photo" role="img" aria-label="Angler in orange jacket holding a landing net" style="background:linear-gradient(160deg,#6f7a5a,#b46a35 55%,#3f4636)"></div><h3>FISHING</h3><p>Lorem ipsum dolor sit amet, consectetur adipiscing elit, sed do eiusmod</p></div>
      <div class="cat"><div class="photo" role="img" aria-label="Golf bag and clubs on a green" style="background:linear-gradient(160deg,#5f8c3a,#9aa89a 55%,#4c7330)"></div><h3>GOLF</h3><p>Lorem ipsum dolor sit amet, consectetur adipiscing elit, sed do eiusmod</p></div>
    </div>
  </div>
</section>

<section class="featured">
  <div class="wrap">
    <h2 class="section-title">Featured Products</h2>
    <svg class="arrow" style="left:-38px;top:208px" width="16" height="30" viewBox="0 0 16 30"><path d="M15 1L1 15l14 14" stroke="#333" stroke-width="2" fill="none"/></svg>
    <svg class="arrow" style="right:-38px;top:208px" width="16" height="30" viewBox="0 0 16 30"><path d="M1 1l14 14L1 29" stroke="#333" stroke-width="2" fill="none"/></svg>
    <div class="prod-row">
      <div class="prod"><div class="photo"><div role="img" aria-label="Grey towel with orange clip holder" style="width:100px;height:220px;background:linear-gradient(180deg,#e08a3a 0 12%,#8a8a8a 12%,#6f6f6f)"></div></div><div class="name">Towel with holder kopiera</div><div class="price">$ 20.39</div></div>
      <div class="prod"><div class="photo"><div role="img" aria-label="Clip-on magnifier glasses on a lanyard" style="width:110px;height:220px;background:linear-gradient(180deg,#333 0 30%,#dcdcea 30%,#c9c9db)"></div></div><div class="name">Nose - magnifiier glasses</div><div class="price">$ 20.39</div></div>
      <div class="prod"><div class="photo"><div role="img" aria-label="Clear tarpaulin weight bag filled with water" style="width:160px;height:160px;background:linear-gradient(160deg,#f2f2f2,#c7c9cc)"></div></div><div class="name">Trapaulin weight bag</div><div class="price">$ 20.39</div></div>
      <div class="prod"><div class="photo"><div role="img" aria-label="Bungee strap with orange hooks" style="width:110px;height:210px;background:linear-gradient(180deg,#e07a20 0 15%,#444 15% 85%,#e07a20 85%)"></div></div><div class="name">Ryckavlastare Rep</div><div class="price">$ 20.39</div></div>
    </div>
  </div>
</section>

<section class="about">
  <div class="photo" role="img" aria-label="Angler in orange jacket reading on a riverbank" style="background:linear-gradient(150deg,#6b7566,#a36238 45%,#3d4440 80%,#77766f)"></div>
  <div class="copy">
    <h2>ABOUT US</h2>
    <p>Lorem ipsum dolor sit amet, consectetur adipiscing elit, sed do eiusmod tempor inciore et dolore magna aliqua. Quis ipsum suspendisse ulvida. Risus commodo viverra maecenas accumsan lacus vel flisis. Lorem ipsum dolor sit amet, consectetur adipiscing sed do eiusmod tempor incididunt ut labore et dolore magna aliqua. Quis ipsum suspendisse ultrices gravida. Risus commodo viverra maecenas accumsan lacus vel facilisis.</p>
    <a class="btn-outline">LEARN MORE</a>
  </div>
</section>

<section class="reviews">
  <div class="wrap">
    <h2 class="section-title">Client Review</h2>
    <div class="rev-row">
      <div class="rev"><div class="who"><span class="avatar" role="img" aria-label="Client portrait"></span><div><b>John Smith</b><div class="stars"><svg width="62" height="11" viewBox="0 0 62 11"><g fill="#f5b400"><path id="s" d="M5.5 0l1.6 3.6 3.9.4-2.9 2.6.8 3.9-3.4-2-3.4 2 .8-3.9L0 4l3.9-.4z"/><use href="#s" x="12.5"/><use href="#s" x="25"/><use href="#s" x="37.5"/><use href="#s" x="50"/></g></svg></div></div></div><p>Lorem ipsum dolor sitntetur adipiscing elit, sed do eimod tempdunt ut labore et dolore maqua. Qusum suspendisse ultrices gravida.</p></div>
      <div class="rev"><div class="who"><span class="avatar" role="img" aria-label="Client portrait"></span><div><b>John Smith</b><div class="stars"><svg width="62" height="11" viewBox="0 0 62 11"><g fill="#f5b400"><use href="#s"/><use href="#s" x="12.5"/><use href="#s" x="25"/><use href="#s" x="37.5"/><use href="#s" x="50"/></g></svg></div></div></div><p>Lorem ipsum dolor sitntetur adipiscing elit, sed do eimod tempdunt ut labore et dolore maqua. Qusum suspendisse ultrices gravida.</p></div>
      <div class="rev"><div class="who"><span class="avatar" role="img" aria-label="Client portrait"></span><div><b>John Smith</b><div class="stars"><svg width="62" height="11" viewBox="0 0 62 11"><g fill="#f5b400"><use href="#s"/><use href="#s" x="12.5"/><use href="#s" x="25"/><use href="#s" x="37.5"/><use href="#s" x="50"/></g></svg></div></div></div><p>Lorem ipsum dolor sitntetur adipiscing elit, sed do eimod tempdunt ut labore et dolore maqua. Qusum suspendisse ultrices gravida.</p></div>
    </div>
  </div>
</section>

<section class="newsletter">
  <div class="wrap">
    <h2>SUBSCRIBE TO OUR NEWSLETTER</h2>
    <div class="news-form"><span class="field">Email Address</span><span class="submit">SUBSCRIBE</span></div>
  </div>
</section>

<section class="blog">
  <div class="wrap">
    <h2 class="section-title">Our Blog</h2>
    <div class="blog-row">
      <div class="post"><div class="photo" role="img" aria-label="White boat interior with steering wheel" style="background:linear-gradient(160deg,#f0f0f0,#a9a9a9 60%,#6d6f72)"></div><h3>Lorem ipsum dolor sit amet, consectet ur adipiscing elit, sed do eiusmod</h3><p>Asmod tempor incididunt ut lab et dolore magna aliqua. Quis ipsum suspndisse ultrices gravida. <a>Read More</a></p></div>
      <div class="post"><div class="photo" role="img" aria-label="Blue weight bags on a jetty by a lake" style="background:linear-gradient(180deg,#9fb6cf 0 30%,#3d5b86 30%,#243d78 70%,#d8dde3)"></div><h3>Lorem ipsum dolor sit amet, consectet ur adipiscing elit, sed do eiusmod</h3><p>Asmod tempor incididunt ut lab et dolore magna aliqua. Quis ipsum suspndisse ultrices gravida. <a>Read More</a></p></div>
      <div class="post"><div class="photo" role="img" aria-label="Covered boat held down with weight bags" style="background:linear-gradient(170deg,#8d98a8,#4a5262 55%,#6f6a60)"></div><h3>Lorem ipsum dolor sit amet, consectet ur adipiscing elit, sed do eiusmod</h3><p>Asmod tempor incididunt ut lab et dolore magna aliqua. Quis ipsum suspndisse ultrices gravida. <a>Read More</a></p></div>
    </div>
  </div>
</section>

<footer class="footer">
  <div class="wrap">
    <div class="foot-brand">
      <div class="brand"><span class="mark"></span>QUIBREL OUTDOOR</div>
      <div class="contact">
        <div><svg width="13" height="13" viewBox="0 0 24 24"><path fill="#fff" d="M6.6 10.8a15 15 0 0 0 6.6 6.6l2.2-2.2a1 1 0 0 1 1-.25 11.4 11.4 0 0 0 3.6.57 1 1 0 0 1 1 1V20a1 1 0 0 1-1 1A17 17 0 0 1 3 4a1 1 0 0 1 1-1h3.5a1 1 0 0 1 1 1c0 1.25.2 2.45.57 3.57a1 1 0 0 1-.25 1z"/></svg>155 204 3817</div>
        <div><svg width="11" height="15" viewBox="0 0 11 15"><path fill="#fff" d="M5.5 0A5.5 5.5 0 0 0 0 5.5C0 9.6 5.5 15 5.5 15S11 9.6 11 5.5A5.5 5.5 0 0 0 5.5 0zm0 7.5a2 2 0 1 1 0-4 2 2 0 0 1 0 4z"/></svg>48 Larkmoor Lane Fernwick USA 30418</div>
        <div><svg width="15" height="12" viewBox="0 0 14 11"><rect x=".6" y=".6" width="12.8" height="9.8" rx="1" stroke="#fff" stroke-width="1.2" fill="none"/><path d="M1 1l6 5 6-5" stroke="#fff" stroke-width="1.2" fill="none"/></svg>info@QuibrelOutdoor.com</div>
      </div>
    </div>
    <div class="col c1"><h4>Quick Link</h4><ul><li>Home</li><li>Shop</li><li>About Us</li><li>Review</li><li>Blog</li><li>Contact Us</li></ul></div>
    <div class="col c2"><h4>Information</h4><ul><li>Login</li><li>My Account</li><li>Terms &amp; Conditions</li><li>Order Tracking</li><li>Payment System</li><li>Promotional Offers</li></ul></div>
    <div class="col"><h4>Follow Us</h4><ul><li>Friendwall</li><li>Chirpline</li><li>Snapgrid</li><li>Workweb</li><li>Circleplus</li><li>Viewtube</li></ul></div>
  </div>
  <div class="bottom">
    <div class="wrap">
      <span>© 2021 Quibrel Outdoor. All Rights Reserved.</span>
      <div class="cards"><span></span><span></span><span></span><span></span><span></span><span></span><span></span><span></span><span></span></div>
    </div>
  </div>
</footer>

</body>
</html>
```